BLS Business Card 2018

Larkmere Chiropractic. We have two locations that we want to advertise on the same card. Brightvale OrthoCore campus address: 3815 Pellham Dr., Suite 240, Flowood, MS 39417. Madison address: 246 Willowmere Dr., Building D., Madison, MS 39284. website: www.drlarkmere-example.com. o:(601)555-0147 f:(601)555-0183

Target Market(s)

Health care decision makers: primary care doctors and mothers

Contact Information for Business Card

I have no idea; up for any suggestions and I'd do much better picking from examples versus describing what I'm looking for. We are in a very high end location and would like the cards to look really sharp.

Requirements
Must have
• My name, Martin R Belvane, D.C.

```html
<!DOCTYPE html>
<html lang="en">
<head>
<meta charset="utf-8">
<title>Larkmere Chiropractic – Business Card</title>
<link rel="stylesheet" href="https://fonts.googleapis.com/css2?family=Cinzel:wght@600&family=Merriweather:wght@700&family=Lato:wght@400&display=swap">
<style>
  :root {
    --backdrop: #e4e4e4;
    --navy: #0c5a7d;
    --teal: #3fb0c4;
    --teal-soft: #5cc3d3;
    --paper: #f7f7f7;
    --ink-light: #ffffff;
    --ink-muted: #cfe3ec;
    --figure-grey: #c9cdd1;
  }
  * { box-sizing: border-box; margin: 0; padding: 0; }
  html, body { width: 1200px; height: 852px; overflow: hidden; }
  body {
    background: var(--backdrop);
    position: relative;
    font-family: "Lato", Arial, sans-serif;
  }
  .card {
    position: absolute;
    width: 520px;
    height: 300px;
    border-radius: 22px;
    overflow: hidden;
    box-shadow: 0 6px 18px rgba(0,0,0,0.18);
  }
  /* Front */
  .card--front { left: 50px; top: 276px; background: var(--navy); }
  .front-figure {
    position: absolute;
    left: 40px; top: 20px;
    width: 200px; height: 280px;
    border-radius: 90px 90px 0 0;
    background: radial-gradient(ellipse at 50% 45%, rgba(92,195,211,0.35), rgba(92,195,211,0) 70%);
  }
  .front-wordmark {
    position: absolute;
    right: 34px; top: 92px;
    font-family: "Cinzel", "Times New Roman", serif;
    font-weight: 600;
    color: var(--ink-light);
    text-transform: uppercase;
    line-height: 1.05;
    font-size: 31px;
    letter-spacing: 0.5px;
  }
  /* Back */
  .card--back { left: 630px; top: 276px; background: var(--navy); }
  .back-shape { position: absolute; inset: 0; }
  .back-figure {
    position: absolute;
    left: 70px; top: 62px;
    width: 96px; height: 98px;
    border-radius: 40px 40px 10px 10px;
    background: radial-gradient(ellipse at 50% 50%, var(--figure-grey), rgba(201,205,209,0) 72%);
  }
  .back-wordmark {
    position: absolute;
    left: 34px; top: 172px;
    font-family: "Cinzel", "Times New Roman", serif;
    font-weight: 600;
    color: var(--navy);
    text-transform: uppercase;
    font-size: 21px;
    line-height: 1.05;
  }
  .contact {
    position: absolute;
    left: 268px; top: 38px;
    color: var(--ink-light);
  }
  .contact__name {
    font-family: "Merriweather", Georgia, serif;
    font-weight: 700;
    font-size: 15px;
  }
  .contact__title {
    font-size: 9px;
    color: var(--ink-muted);
    margin-top: 2px;
    margin-bottom: 22px;
  }
  .contact__list { list-style: none; }
  .contact__item {
    display: flex;
    align-items: flex-start;
    gap: 9px;
    font-size: 11.5px;
    line-height: 14px;
    margin-bottom: 3px;
  }
  .contact__item svg { flex: 0 0 11px; width: 11px; height: 11px; margin-top: 1.5px; fill: var(--ink-light); }
</style>
</head>
<body>

  <section class="card card--front" aria-label="Business card front">
    <div class="front-figure" role="img" aria-label="Line drawing of a stretching human torso"></div>
    <div class="front-wordmark">Larkmere<br>Chiropractic</div>
  </section>

  <section class="card card--back" aria-label="Business card back">
    <svg class="back-shape" viewBox="0 0 520 300" aria-hidden="true">
      <path d="M0 0 H150 C225 60 250 180 232 300 H0 Z" fill="var(--teal)"/>
      <path d="M0 0 H138 C212 62 236 182 218 300 H0 Z" fill="var(--paper)"/>
    </svg>
    <div class="back-figure" role="img" aria-label="Line drawing of a stretching human torso"></div>
    <div class="back-wordmark">Larkmere<br>Chiropractic</div>

    <div class="contact">
      <p class="contact__name">Martin R Belvane, D.C.</p>
      <p class="contact__title">Managing Director</p>
      <ul class="contact__list">
        <li class="contact__item">
          <svg viewBox="0 0 12 12"><path d="M2.5 1 L4.5 1 L5.5 3.5 L4.2 4.5 C4.8 5.9 6 7.2 7.5 7.8 L8.5 6.5 L11 7.5 L11 9.5 C11 10.3 10.3 11 9.5 11 C5 11 1 7 1 2.5 C1 1.7 1.7 1 2.5 1 Z"/></svg>
          <span>(601)555-0147</span>
        </li>
        <li class="contact__item">
          <svg viewBox="0 0 12 12"><rect x="3" y="1" width="6" height="3"/><rect x="1" y="4.5" width="10" height="4.5" rx="1"/><rect x="3" y="8" width="6" height="3"/></svg>
          <span>(601)555-0183</span>
        </li>
        <li class="contact__item">
          <svg viewBox="0 0 12 12"><rect x="1" y="2.5" width="10" height="7" rx="1"/><path d="M1.5 3 L6 6.5 L10.5 3" fill="none" stroke="var(--navy)" stroke-width="1"/></svg>
          <span>m.r.belvane@drlarkmere-example.com</span>
        </li>
        <li class="contact__item">
          <svg viewBox="0 0 12 12"><circle cx="6" cy="6" r="5"/><path d="M1 6 H11 M6 1 C3.5 3.5 3.5 8.5 6 11 M6 1 C8.5 3.5 8.5 8.5 6 11" fill="none" stroke="var(--navy)" stroke-width="0.8"/></svg>
          <span>www.drlarkmere-example.com</span>
        </li>
        <li class="contact__item">
          <svg viewBox="0 0 12 12"><path d="M6 0.5 C3.8 0.5 2.2 2.2 2.2 4.3 C2.2 7 6 11.5 6 11.5 C6 11.5 9.8 7 9.8 4.3 C9.8 2.2 8.2 0.5 6 0.5 Z"/><circle cx="6" cy="4.3" r="1.4" fill="var(--navy)"/></svg>
          <span>3815 Pellham Dr., Suite 240,<br>Flowood, MS 39417</span>
        </li>
        <li class="contact__item">
          <svg viewBox="0 0 12 12"><path d="M6 0.5 C3.8 0.5 2.2 2.2 2.2 4.3 C2.2 7 6 11.5 6 11.5 C6 11.5 9.8 7 9.8 4.3 C9.8 2.2 8.2 0.5 6 0.5 Z"/><circle cx="6" cy="4.3" r="1.4" fill="var(--navy)"/></svg>
          <span>246 Willowmere Dr., Building D.,<br>Madison, MS 39284</span>
        </li>
      </ul>
    </div>
  </section>

</body>
</html>
```